stationary deign for trucking company

im a trucking company looking for a professional set of stationary designs i deliver goods from point a to b
Updates

When submitting stationary designs I need envelope design, letterhead, cards, I’d badge etc

Industry/Entity Type

Trucking Company

Requirements
Must have
• must have letter head, business card, envelope, fax sheet, id badge, folder, thank you card, notebook, invoice sheet.
Nice to have
• nice to have them all custom made (letterhead,envelope, business card, I’d badge etc
Should not have
• must not have prepaid sign want i unique design for items

```html
<!DOCTYPE html>
<html lang="en">
<head>
<meta charset="utf-8">
<title>Brennick Freight — Stationery Set</title>
<link href="https://fonts.googleapis.com/css2?family=Montserrat:wght@500;600;700&family=Open+Sans:wght@400;600;700&display=swap" rel="stylesheet">
<style>
  :root {
    --bg: #dcdad8;
    --ink: #111111;
    --paper: #ffffff;
    --blue: #1e5fb0;
    --blue-deep: #2f4a9a;
    --navy: #0d2f6b;
    --grey-text: #8a8a8a;
    --band: #4a4a4a;
  }
  * { box-sizing: border-box; margin: 0; padding: 0; }
  html, body { width: 1200px; height: 904px; overflow: hidden; background: var(--bg); }
  body { position: relative; font-family: "Open Sans", Arial, sans-serif; color: var(--ink); }
  .piece { position: absolute; box-shadow: 0 4px 10px rgba(0,0,0,.18); }

  .brand { display: flex; align-items: center; gap: 7px; font-family: "Montserrat", Arial, sans-serif; font-weight: 600; letter-spacing: .12em; white-space: nowrap; }
  .brand-mark { display: inline-block; flex: none; background: currentColor; }
  .brand--dark { color: var(--ink); }
  .brand--light { color: var(--paper); }

  /* Letterhead */
  .letterhead { left: 100px; top: 28px; width: 345px; height: 490px; background: var(--paper); }
  .letterhead .brand { position: absolute; left: 22px; top: 42px; font-size: 13px; }
  .letterhead .brand-mark { width: 12px; height: 12px; }
  .letterhead-contact { position: absolute; left: 230px; top: 16px; padding-left: 8px; border-left: 1px solid #ccc; font-size: 5.5px; line-height: 10px; color: var(--navy); }
  .letterhead-contact .strong { font-weight: 700; color: var(--blue); }
  .letterhead-body { position: absolute; left: 38px; top: 110px; width: 270px; font-size: 6.2px; line-height: 10.8px; color: var(--grey-text); }
  .letterhead-body p { margin-bottom: 11px; }
  .letterhead-foot { position: absolute; left: 0; right: 0; bottom: 0; height: 3px; background: linear-gradient(90deg, var(--ink) 0 78%, var(--paper) 78% 79%, var(--blue) 79%); }

  /* Folder */
  .folder { left: 436px; top: 72px; width: 344px; height: 490px; background: var(--ink); }
  .folder .brand { position: absolute; left: 40px; top: 224px; font-size: 27px; letter-spacing: .1em; }
  .folder .brand-mark { width: 26px; height: 26px; }
  .folder-tagline { position: absolute; left: 108px; top: 256px; font-family: "Montserrat", Arial, sans-serif; font-size: 9px; letter-spacing: .28em; color: var(--paper); }
  .folder-url { position: absolute; left: 0; right: 0; bottom: 8px; text-align: center; font-weight: 700; font-size: 7.5px; color: var(--paper); }
  .folder-foot { position: absolute; left: 0; right: 0; bottom: 0; height: 3px; background: linear-gradient(90deg, #555 0 38%, var(--blue) 38% 70%, #555 70%); }

  /* Business cards */
  .card-front { left: 828px; top: 76px; width: 158px; height: 92px; background: var(--ink); overflow: hidden; }
  .card-front .brand { position: absolute; left: 0; right: 0; top: 0; bottom: 0; justify-content: center; gap: 6px; font-size: 8px; letter-spacing: .08em; }
  .card-front .brand-mark { width: 8px; height: 8px; }
  .card-back { left: 830px; top: 206px; width: 155px; height: 88px; background: var(--paper); overflow: hidden; }
  .card-back .brand { position: absolute; left: 10px; top: 38px; font-size: 7.5px; letter-spacing: .08em; }
  .card-back .brand-mark { width: 7px; height: 7px; }
  .card-back-details { position: absolute; left: 80px; top: 16px; padding-left: 5px; border-left: 1px solid #bbb; font-size: 3.6px; line-height: 6px; color: var(--navy); }
  .card-back-details .name { font-size: 4.6px; font-weight: 700; color: var(--blue); }
  .card-back-foot { position: absolute; left: 0; right: 0; bottom: 0; height: 3px; background: linear-gradient(90deg, var(--blue) 0 45%, var(--ink) 45%); }

  /* Notebook */
  .notebook { left: 830px; top: 328px; width: 146px; height: 230px; background: var(--ink); border-radius: 3px 9px 9px 3px; }
  .notebook .brand { position: absolute; left: 14px; top: 110px; font-size: 11px; letter-spacing: .08em; }
  .notebook .brand-mark { width: 8px; height: 8px; }
  .notebook-band { position: absolute; left: 102px; top: 0; width: 6px; height: 100%; background: var(--band); }
  .notebook-url { position: absolute; left: 44px; bottom: 5px; font-size: 3.6px; font-weight: 700; color: var(--paper); }

  /* Thank you card */
  .thanks { left: 72px; top: 592px; width: 340px; height: 240px; background: var(--paper); overflow: hidden; }
  .thanks-art { position: absolute; inset: 0; }
  .thanks .brand { position: absolute; left: 118px; top: 150px; font-size: 22px; letter-spacing: .1em; }
  .thanks .brand-mark { width: 18px; height: 18px; }
  .thanks-foot { position: absolute; left: 0; right: 0; bottom: 0; height: 16px; background: var(--ink); color: var(--paper); font-size: 5px; line-height: 16px; padding-left: 10px; white-space: nowrap; overflow: hidden; }

  /* Pen */
  .pen { left: 250px; top: 842px; width: 320px; height: 22px; background: linear-gradient(180deg, #fff, #e6e6ea); border-radius: 3px 12px 12px 3px; }
  .pen .brand { position: absolute; left: 100px; top: 5px; font-size: 9px; }
  .pen .brand-mark { width: 7px; height: 7px; }

  /* ID badge */
  .badge { left: 440px; top: 666px; width: 296px; height: 152px; background: var(--paper); border-radius: 6px; border: 6px solid #eeeeee; }
  .badge-photo { position: absolute; left: 12px; top: 8px; width: 92px; height: 92px; background: linear-gradient(180deg, #e8e8ea, #3b3f4a); }
  .badge .brand { position: absolute; left: 132px; top: 50px; font-size: 13px; letter-spacing: .12em; }
  .badge .brand-mark { width: 10px; height: 10px; }
  .badge-band { position: absolute; left: 0; right: 0; bottom: 0; height: 38px; background: var(--blue); color: var(--paper); border-top: 2px solid #dde; }
  .badge-name { position: absolute; left: 18px; top: 6px; font-weight: 700; font-size: 10px; }
  .badge-role { position: absolute; left: 18px; top: 20px; font-size: 7px; }
  .badge-card { position: absolute; right: 18px; top: 6px; font-size: 8px; text-align: center; line-height: 12px; }

  /* Envelope */
  .envelope-back { left: 796px; top: 594px; width: 355px; height: 215px; background: var(--paper); box-shadow: 0 3px 8px rgba(0,0,0,.15); }
  .envelope-flap { position: absolute; left: 0; top: 0; width: 100%; height: 60px; background: linear-gradient(180deg, #3b73c4, var(--blue)); border-radius: 18px 18px 0 0; }
  .envelope-front { left: 760px; top: 676px; width: 356px; height: 176px; background: var(--paper); }
  .envelope-front .brand { position: absolute; left: 14px; top: 24px; font-size: 12px; }
  .envelope-front .brand-mark { width: 10px; height: 10px; }
  .envelope-address { position: absolute; left: 12px; top: 44px; font-size: 5px; font-weight: 700; color: var(--navy); }
  .envelope-foot { position: absolute; left: 0; right: 0; bottom: 0; height: 3px; background: linear-gradient(90deg, var(--ink) 0 38%, var(--blue) 38% 78%, var(--ink) 78%); }
</style>
</head>
<body>

  <section class="piece letterhead" aria-label="Letterhead">
    <div class="brand brand--dark"><span class="brand-mark"></span>BRENNICK FREIGHT</div>
    <div class="letterhead-contact">
      <div class="strong">Level 00, 00 Harbour Street,</div>
      <div class="strong">Example, 000</div>
      <div>0000 000 000 &nbsp; 0000 000 000</div>
      <div>contact@brennickfreight.com</div>
      <div>www.brennickfreight.com</div>
    </div>
    <div class="letterhead-body">
      <p>Lorem Ipsum is simply dummy text of the printing and typesetting industry. Lorem Ipsum has been the industry's standard dummy text ever since the 1500s, when an unknown printer took a galley of type and scrambled it to make a type specimen book. It has survived not only five centuries, but also the leap into electronic typesetting, remaining essentially unchanged.</p>
      <p>It is a long established fact that a reader will be distracted by the readable content of a page when looking at its layout. The point of using Lorem Ipsum is that it has a more-or-less normal distribution of letters, as opposed to using 'Content here, content here', making it look like readable English. Various versions have evolved over the years, sometimes by accident, sometimes on purpose.</p>
      <p>Contrary to popular belief, Lorem Ipsum is not simply random text. It has roots in a piece of classical Latin literature from 45 BC, making it over 2000 years old. The generated Lorem Ipsum is therefore always free from repetition, injected humour, or non-characteristic words etc.</p>
    </div>
    <div class="letterhead-foot"></div>
  </section>

  <section class="piece folder" aria-label="Presentation folder">
    <div class="brand brand--light"><span class="brand-mark"></span>BRENNICK</div>
    <div class="folder-tagline">FREIGHT LINES</div>
    <div class="folder-url">www.brennickfreight.com</div>
    <div class="folder-foot"></div>
  </section>

  <section class="piece card-front" aria-label="Business card front">
    <div class="brand brand--light"><span class="brand-mark"></span>BRENNICK FREIGHT</div>
  </section>

  <section class="piece card-back" aria-label="Business card back">
    <div class="brand brand--dark"><span class="brand-mark"></span>BRENNICK</div>
    <div class="card-back-details">
      <div class="name">Example Name</div>
      <div>Designation</div>
      <div>Level 00, 00 Harbour St, Example</div>
      <div>0000 000 000 &nbsp; 0000 000 000</div>
      <div>info@brennickfreight.com</div>
      <div>www.brennickfreight.com</div>
    </div>
    <div class="card-back-foot"></div>
  </section>

  <section class="piece notebook" aria-label="Notebook">
    <div class="brand brand--light"><span class="brand-mark"></span>BRENNICK</div>
    <div class="notebook-band"></div>
    <div class="notebook-url">www.brennickfreight.com</div>
  </section>

  <section class="piece thanks" aria-label="Thank you card">
    <svg class="thanks-art" width="340" height="240" viewBox="0 0 340 240" role="img" aria-label="Blue swoosh panel carrying handwritten thank you lettering">
      <defs>
        <linearGradient id="thanksBlue" x1="0" y1="0" x2="1" y2="1">
          <stop offset="0" stop-color="#2b3f8c"/>
          <stop offset="1" stop-color="#6d86c9"/>
        </linearGradient>
      </defs>
      <path d="M0 0 H340 V10 C250 20 170 40 120 100 C80 150 60 200 40 240 H0 Z" fill="url(#thanksBlue)"/>
      <path d="M340 10 C250 20 170 40 120 100 C80 150 60 200 40 240" fill="none" stroke="#cfd3dc" stroke-width="3"/>
    </svg>
    <div class="brand brand--dark"><span class="brand-mark"></span>BRENNICK</div>
    <div class="thanks-foot">001 Example Dr, Example Bay, EX 00000 &nbsp; 000-000-0000 &nbsp; contact@brennickfreight.com &nbsp; www.brennickfreight.com</div>
  </section>

  <section class="piece pen" aria-label="Branded pen">
    <div class="brand brand--dark"><span class="brand-mark"></span>BRENNICK</div>
  </section>

  <section class="piece badge" aria-label="Employee ID badge">
    <div class="badge-photo" role="img" aria-label="Employee portrait photo"></div>
    <div class="brand brand--dark"><span class="brand-mark"></span>BRENNICK</div>
    <div class="badge-band">
      <div class="badge-name">Employee Name</div>
      <div class="badge-role">Employee Designation</div>
      <div class="badge-card">Card Number<br>0000000000000000</div>
    </div>
  </section>

  <section class="piece envelope-back" aria-label="Envelope back">
    <div class="envelope-flap" role="img" aria-label="Blue patterned envelope flap"></div>
  </section>

  <section class="piece envelope-front" aria-label="Envelope front">
    <div class="brand brand--dark"><span class="brand-mark"></span>BRENNICK FREIGHT</div>
    <div class="envelope-address">Level 00, 00 Example Street, Example, 2000</div>
    <div class="envelope-foot"></div>
  </section>

</body>
</html>
```